website redesign - tallowgrange.com.au

need to redesign our website. we are proud of our current website but market feedback suggests that we have to tone down our quirkiness and make it look more professional to target the million dollar market.
right now we appeal to the younger generation so we have to meet somewhere in the middle.
we want to still retain our same flavour and style but need to also look a bit more professional. we need to evolve our brand to a more grown up look.
examples of standard websites include copperleaf property, wren property, lodging ledger, pellings onward, dunmore

```html
<!DOCTYPE html>
<html lang="en">
<head>
<meta charset="utf-8">
<title>Tallowgrange Realty</title>
<link href="https://fonts.googleapis.com/css2?family=Montserrat:wght@400;500;600;700&family=Arimo:wght@400&display=swap" rel="stylesheet">
<style>
:root{
  --orange:#ee5a24;
  --orange-deep:#e5441c;
  --orange-light:#f47a3a;
  --ink:#2b2b2b;
  --muted:#666;
  --pale:#f3f3f3;
  --dark:#1a1a1a;
  --white:#fff;
}
*{box-sizing:border-box;margin:0;padding:0}
html,body{width:1200px;height:4758px;overflow:hidden}
body{position:relative;background:var(--white);font-family:"Arimo",Arial,sans-serif;color:var(--ink)}
.abs{position:absolute}
.head{font-family:"Montserrat",sans-serif}
.center{text-align:center;left:0;width:1200px}
.accent{color:var(--orange)}

/* header */
.brand{font-family:"Montserrat",sans-serif;font-weight:600;letter-spacing:1px}
.site-header .brand{left:111px;top:34px;font-size:27px;color:var(--ink);display:flex;align-items:center;gap:10px}
.brand .dot{width:14px;height:14px;background:var(--orange);display:inline-block}
.call{right:110px;top:22px;display:flex;align-items:center;gap:12px;font-family:"Montserrat",sans-serif;font-size:17px;font-weight:500}
.call .ring{width:62px;height:62px;border:2px solid var(--orange);border-radius:50%;display:flex;align-items:center;justify-content:center}
.main-nav{top:107px;left:0;width:1200px;height:61px;background:linear-gradient(90deg,var(--orange),var(--orange-deep))}
.main-nav ul{list-style:none;display:flex;position:absolute;left:111px;top:0;height:61px}
.main-nav li{font-family:"Montserrat",sans-serif;font-size:12px;font-weight:600;color:var(--white);padding:0 26px;line-height:61px}
.main-nav li.on{background:#2a2a2a}

/* hero */
.hero{top:168px;left:0;width:1200px;height:712px;background:linear-gradient(180deg,#cfd6de 0%,#a9a39a 45%,#5a4a3a 70%,#2f6f8a 100%)}
.hero-panel{left:273px;top:275px;width:654px;height:110px;background:rgba(40,40,40,.55)}
.hero h1{top:300px;font-family:"Montserrat",sans-serif;font-weight:600;font-size:54px;color:var(--white);letter-spacing:1px}
.hero .tag{top:378px;font-family:"Montserrat",sans-serif;font-weight:600;font-size:26px;color:var(--white)}
.btn{background:var(--orange);color:var(--white);font-family:"Montserrat",sans-serif;font-weight:600;text-align:center;border-radius:3px}
.hero .btn{left:531px;top:435px;width:138px;height:48px;line-height:48px;font-size:15px}

/* welcome */
.eyebrow{font-family:"Montserrat",sans-serif;font-weight:500;font-size:21px}
.script-title{font-family:"Montserrat",sans-serif;font-weight:500;font-size:36px;color:var(--orange)}
.lead{font-size:12.5px;line-height:28px;color:var(--muted)}
.service{width:300px;text-align:center}
.service .disc{width:134px;height:134px;margin:0 auto;border-radius:50%;border:3px solid var(--orange);display:flex;align-items:center;justify-content:center}
.service .disc span{width:114px;height:114px;border-radius:50%;background:var(--orange);display:flex;align-items:center;justify-content:center}
.service h3{font-family:"Montserrat",sans-serif;font-weight:500;font-size:19px;margin-top:22px}
.service p{font-size:12.5px;line-height:26px;color:var(--muted);margin-top:12px}

/* property */
.property-band{top:1458px;left:0;width:1200px;height:850px;background:var(--pale)}
.section-title{font-family:"Montserrat",sans-serif;font-weight:600;font-size:34px}
.rule{width:46px;height:3px;background:var(--orange);left:577px}
.card{top:1588px;width:308px;height:509px;background:var(--white);border:1px solid #ddd;text-align:center}
.card .photo{margin:8px;height:231px}
.card h4{font-family:"Montserrat",sans-serif;font-weight:500;font-size:14px;line-height:25px;margin-top:16px;padding:0 30px}
.card .meta{font-family:"Montserrat",sans-serif;font-size:11px;margin-top:8px;display:flex;justify-content:center;gap:14px}
.card .meta i{display:inline-block;width:14px;height:8px;background:var(--orange);margin-right:6px;border-radius:2px}
.card p{font-size:12.5px;line-height:25px;color:var(--muted);margin-top:14px;padding:0 22px}
.card .price{position:absolute;bottom:0;left:0;width:100%;border-top:1px solid #e4e4e4;height:58px;line-height:58px;font-family:"Montserrat",sans-serif;font-weight:500;font-size:21px;color:var(--orange)}

/* reviews */
.reviews{top:2250px;left:0;width:1200px;height:584px}
.reviews h2{top:128px;font-family:"Montserrat",sans-serif;font-weight:500;font-size:37px;color:var(--white)}
.reviews .sub{top:180px;font-family:"Montserrat",sans-serif;font-size:26px;color:var(--white)}
.quote{top:251px;width:314px;height:213px;background:var(--white);padding:18px 20px}
.quote .q{font-family:"Montserrat",sans-serif;font-weight:700;font-size:22px;color:#555}
.quote .stars{color:var(--orange);font-size:13px;margin-left:8px;letter-spacing:1px}
.quote p{font-size:12px;line-height:23px;color:var(--muted);margin-top:6px;text-align:justify}
.quote:after{content:"";position:absolute;left:54px;bottom:-14px;border-left:14px solid transparent;border-right:0;border-top:14px solid var(--white)}
.reviewer{top:499px;color:var(--white)}
.reviewer b{display:block;font-family:"Montserrat",sans-serif;font-weight:600;font-size:15px}
.reviewer span{font-size:12px;display:block;margin-top:10px}

/* video */
.video-frame{left:484px;top:2935px;width:605px;height:410px;border:1px solid #bbb}
.video-still{left:111px;top:2907px;width:498px;height:375px;background:linear-gradient(135deg,#2b1d6b,#7a3fd0 45%,#1b1030)}
.play{left:310px;top:3046px;width:98px;height:98px;border:3px solid var(--white);border-radius:50%;background:rgba(0,0,0,.35)}
.video-copy{left:652px;top:2980px;width:388px}
.video-copy .e{font-family:"Montserrat",sans-serif;font-weight:500;font-size:17px}
.video-copy .t{font-family:"Montserrat",sans-serif;font-weight:500;font-size:22px;color:var(--orange);margin-top:10px}
.video-copy p{font-size:12px;line-height:25.5px;color:var(--muted);margin-top:18px}
.video-copy .btn{display:block;width:147px;height:52px;line-height:52px;font-size:13px;font-weight:500;margin-top:18px}

/* team */
.team-band{top:3415px;left:0;width:1200px;height:508px;background:var(--pale)}
.team-photo{left:126px;top:3701px;width:954px;height:222px;background:linear-gradient(180deg,#e8e8e8,#9c8d82 60%,#2c2c34)}

/* contact */
.contact{top:3923px;left:0;width:1200px;height:560px;background:linear-gradient(180deg,#f1f1f1,#d9d9d9 60%,#c4c4c4)}
.field{height:52px;background:var(--white);border:1px solid #bbb;font-size:15px;padding:0 20px;line-height:52px;color:#444}

/* footer */
.site-footer{top:4420px;left:0;width:1200px;height:338px}
.site-footer .brand{top:99px;font-size:34px;color:var(--white);display:flex;justify-content:center;align-items:center;gap:12px}
.foot-nav{top:160px;display:flex;justify-content:center;gap:36px;font-family:"Montserrat",sans-serif;font-weight:500;font-size:12px;color:var(--white)}
.social{top:222px;display:flex;justify-content:center;gap:8px}
.social span{width:36px;height:36px;border:2px solid var(--white);border-radius:50%}
.copy{top:282px;font-family:"Montserrat",sans-serif;font-size:15px;color:var(--white)}
</style>
</head>
<body>

<header class="site-header">
  <div class="abs brand"><i class="dot"></i>TALLOWGRANGE REALTY</div>
  <div class="abs call">
    <span class="ring"><svg width="20" height="20" viewBox="0 0 24 24"><path d="M6.6 10.8a15 15 0 006.6 6.6l2.2-2.2c.3-.3.7-.4 1-.2 1.1.4 2.3.6 3.6.6.6 0 1 .4 1 1V20c0 .6-.4 1-1 1A17 17 0 013 4c0-.6.4-1 1-1h3.5c.6 0 1 .4 1 1 0 1.3.2 2.5.6 3.6.1.3 0 .7-.2 1z" fill="#ee5a24"/></svg></span>
    Call us : 0491 570 156
  </div>
</header>
<nav class="abs main-nav">
  <ul><li class="on">HOME</li><li>ABOUT US</li><li>PROPERTIES</li><li>WHY SELL WITH US?</li><li>PROPERTY MANAGEMENT</li><li>REVIEWS</li><li>CONTACT US</li></ul>
</nav>

<section class="abs hero" role="img" aria-label="Modern two-storey luxury home with pool at dusk">
  <div class="abs hero-panel"></div>
  <h1 class="abs center">TALLOWGRANGE REALTY</h1>
  <div class="abs center tag">THE BEST PROPERTY EXPERIENCE</div>
  <div class="abs btn">READ MORE</div>
  <svg class="abs" style="left:0;bottom:0" width="1200" height="120" viewBox="0 0 1200 120"><path d="M0 80 C250 125 420 40 620 40 C820 40 980 100 1200 60 L1200 120 L0 120Z" fill="#fff"/></svg>
</section>

<section class="welcome">
  <div class="abs center eyebrow" style="top:888px">WELCOME TO</div>
  <div class="abs center script-title" style="top:915px">Tallowgrange Realty</div>
  <p class="abs center lead" style="top:987px;left:270px;width:660px">So what did Brisbane needs saving from? Other agencies that just didn't care. They all used stale and antiquated marketing. They also just seemed as if they wanted to avoid their clients' needs, and they just made whole process seem so complicated.</p>
  <div class="abs service" style="left:122px;top:1123px">
    <div class="disc"><span><svg width="56" height="56" viewBox="0 0 56 56" fill="none" stroke="#fff" stroke-width="3"><circle cx="28" cy="28" r="18"/><circle cx="22" cy="22" r="3"/><circle cx="34" cy="34" r="3"/><path d="M35 21L21 35"/></svg></span></div>
    <h3>FOR SALE</h3><p>Sed ut perspiciatis unde omnis iste natus error sit voluptatem accusantium omnis iste doloremque</p>
  </div>
  <div class="abs service" style="left:450px;top:1123px">
    <div class="disc"><span><svg width="56" height="56" viewBox="0 0 56 56" fill="none" stroke="#fff" stroke-width="3"><path d="M10 28L28 12l18 16M15 24v20h26V24"/><path d="M21 32h14"/></svg></span></div>
    <h3>FOR RENT</h3><p>Sed ut perspiciatis unde omnis iste natus error sit voluptatem accusantium omnis iste doloremque</p>
  </div>
  <div class="abs service" style="left:777px;top:1123px">
    <div class="disc"><span><svg width="56" height="56" viewBox="0 0 56 56" fill="none" stroke="#fff" stroke-width="3"><path d="M14 10h20l8 8v28H14z"/><path d="M20 24h16M20 31h16M20 38h10"/></svg></span></div>
    <h3>OTHER</h3><p>Sed ut perspiciatis unde omnis iste natus error sit voluptatem accusantium omnis iste doloremque</p>
  </div>
</section>

<section class="abs property-band"></section>
<h2 class="abs center section-title" style="top:1502px">OUR <span class="accent">PROPERTY</span></h2>
<div class="abs rule" style="top:1556px"></div>
<article class="abs card" style="left:111px">
  <div class="photo" role="img" aria-label="Two-storey brick house with driveway" style="background:linear-gradient(180deg,#8fb0d0,#8a6c55 60%,#a7a7a7)"></div>
  <h4>14 BANKSIA COURT,<br>WYNNUM, QLD 4178</h4>
  <div class="meta"><span><i></i>(04)</span><span><i></i>(02)</span><span><i></i>(02)</span></div>
  <p>A large balcony perfect for entertaining leads down into a massive backyard with a steel shed and extra tool shed.</p>
  <div class="price">$549,000</div>
</article>
<article class="abs card" style="left:445px">
  <div class="photo" role="img" aria-label="Bright living room interior" style="background:linear-gradient(180deg,#f2f2f2,#d9d9d9 60%,#3b3f55)"></div>
  <h4>U3/40 FERNCLIFF STREET,<br>KELVIN GROVE, QLD 4059</h4>
  <div class="meta"><span><i></i>(04)</span><span><i></i>(02)</span><span><i></i>(02)</span></div>
  <p>A large balcony perfect for entertaining leads down into a massive backyard with a steel shed and extra tool shed.</p>
  <div class="price">$240,000</div>
</article>
<article class="abs card" style="left:779px">
  <div class="photo" role="img" aria-label="Apartment kitchen and dining area" style="background:linear-gradient(180deg,#9aa3ad,#7d6b5c 60%,#5a4a3e)"></div>
  <h4>U7/22 QUARRY LANE,<br>WOOLLOONGABBA, QLD 4102</h4>
  <div class="meta"><span><i></i>(04)</span><span><i></i>(02)</span><span><i></i>(02)</span></div>
  <p>A large balcony perfect for entertaining leads down into a massive backyard with a steel shed and extra tool shed.</p>
  <div class="price">$299,000</div>
</article>
<div class="abs btn" style="left:498px;top:2143px;width:204px;height:59px;line-height:59px;font-size:16px;font-weight:500">VIEW MORE</div>

<section class="abs reviews">
  <svg class="abs" style="left:0;top:0" width="1200" height="584" viewBox="0 0 1200 584"><defs><linearGradient id="rv" x1="0" x2="1"><stop offset="0" stop-color="#f47a3a"/><stop offset="1" stop-color="#e5441c"/></linearGradient></defs><path d="M0 80 C200 20 380 40 600 70 C820 100 1000 40 1200 20 L1200 584 L0 584Z" fill="url(#rv)"/></svg>
  <h2 class="abs center">BUT DON'T JUST TAKE</h2>
  <div class="abs center sub">OUR WORD FOR IT...</div>
  <div class="abs quote" style="left:111px"><span class="q">“</span><span class="stars">★★★★★</span><p>My husband &amp; I were looking for investment properties and the I first moment I spoke to Dev, I already felt comfortable. He was very friendly yet professional, supportive and delivered a quick service overall.</p></div>
  <div class="abs quote" style="left:443px"><span class="q">“</span><span class="stars">★★★★★</span><p>Amazing service, had our property rented out and received comprehensive reports quarterly to make sure the tenant were taking care of our property. Definitely will recommend Tallowgrange to my friends</p></div>
  <div class="abs quote" style="left:775px"><span class="q">“</span><span class="stars">★★★★★</span><p>Tallowgrange are really personal in their approach and did not put a foot wrong in finding me a lovely tenant for my unit in a very short time. Tess is always on the ball and so understanding and helpful. Great job!</p></div>
  <div class="abs reviewer" style="left:111px"><b>RINA DELACORTE</b><span>Sed ut perspiciatis unde</span></div>
  <div class="abs reviewer" style="left:443px"><b>MARIS ELLORY</b><span>Sed ut perspiciatis unde</span></div>
  <div class="abs reviewer" style="left:775px"><b>JUDITH WRENFIELD</b><span>Sed ut perspiciatis unde</span></div>
</section>

<section class="video">
  <div class="abs video-frame"></div>
  <div class="abs video-still" role="img" aria-label="Concert crowd under purple stage lights"></div>
  <div class="abs play"><svg width="92" height="92" viewBox="0 0 92 92"><path d="M36 28L64 46 36 64Z" fill="#fff"/></svg></div>
  <div class="abs video-copy">
    <div class="e">WE KNOW HOW TO</div>
    <div class="t">SHOW OFF A PROPERTY!</div>
    <p>Our videos are different. With everyone searching for new properties online, we don't just want to capture their attention and stand out from the crowd, we want to leave a long-lasting impression. We also promote the lifestyle. Not just the property. New bars, the best restaurants, all of it! We do that by always being ourselves. With our property videos...</p>
    <span class="btn">WATCH VIDEO</span>
  </div>
</section>

<section class="abs team-band"></section>
<h2 class="abs center section-title" style="top:3476px;font-weight:500">SAY HELLO TO <span class="accent">#TEAMTALLOWGRANGE</span></h2>
<p class="abs center lead" style="top:3558px;left:250px;width:700px;font-size:12.5px;line-height:26px">We're a team of Super Agents who mean business about giving you the best property management experience. Unlike other superheroes that get their powers from a spider bite or from groovy gadgets, it is your happiness and satisfaction that drives us. We take the time to get to know our clients well so we can give you the best customised experience and to turn your properties into profits and dreams.</p>
<div class="abs team-photo" role="img" aria-label="Row of eight smiling team members"></div>

<section class="abs contact" role="img" aria-label="Faded city skyline backdrop"></section>
<h2 class="abs center section-title" style="top:3972px;font-weight:500">GET IN <span class="accent">TOUCH WITH US!</span></h2>
<div class="abs field" style="left:146px;top:4065px;width:290px">Name</div>
<div class="abs field" style="left:452px;top:4065px;width:290px">Email address</div>
<div class="abs field" style="left:757px;top:4065px;width:290px">Phone Number</div>
<div class="abs field" style="left:146px;top:4131px;width:901px;height:111px;line-height:40px">Message</div>
<div class="abs btn" style="left:524px;top:4270px;width:152px;height:53px;line-height:53px;font-size:19px;font-weight:500">SUBMIT</div>

<footer class="abs site-footer">
  <svg class="abs" style="left:0;top:0" width="1200" height="338" viewBox="0 0 1200 338"><path d="M0 40 C300 0 500 50 700 45 C900 40 1050 0 1200 10 L1200 338 L0 338Z" fill="#1a1a1a"/></svg>
  <div class="abs center brand"><i class="dot"></i>TALLOWGRANGE REALTY</div>
  <div class="abs center foot-nav"><span>HOME</span><span>ABOUT US</span><span>PROPERTIES</span><span>WHY SELL WITH US?</span><span>PROPERTY MANAGEMENT</span><span>REVIEWS</span><span>CONTACT US</span></div>
  <div class="abs center social"><span></span><span></span><span></span><span></span><span></span></div>
  <div class="abs center copy">Copyright © 2020 Tallowgrange Realty. All right reserved</div>
</footer>

</body>
</html>
```